Tidemark Builders Business Card Design

We need a business card for an established builder of high quality bespoke homes in Auckland and Northland. We build and renovate homes collaboratively facilitating effective communication between owners, builders, architects, suppliers and tradespeople. We have never built or renovated a home that leaks or has faults. We only use reliable materials. We have never been sued or had legal action taken against us. We are honest builders of bespoke homes not group mass produced homes. Our niche market is in character homes. We practice sustainability and have built a lot of coastal property. We have been in business for over thirty years . We would like to see natural colors of the environment sand,sea and maybe vegetation . The design should communicate quality, sustainability,fair pricing, open communication and the originality of bespoke building. And the fact that the builder is registered.

Industry/Entity Type

Business

Contact Information for Business Card

Rowan Tellick Builders
Ph. 021583917
18 Kestrel Rd Harwood Bay Auckland 0814
PO Box 927 Mangawhai 0583

```html
<!DOCTYPE html>
<html lang="en">
<head>
<meta charset="utf-8">
<title>Tidemark Builders – Business Card</title>
<link rel="stylesheet" href="https://fonts.googleapis.com/css2?family=Source+Sans+3:wght@400;600&display=swap">
<style>
  :root {
    --backdrop: #2b2b2d;
    --card: #1c1c1f;
    --brand-blue: #3a78cf;
    --ring-grey: #9a9a9c;
    --text-light: #f1f1f1;
  }
  * { box-sizing: border-box; margin: 0; padding: 0; }
  html, body {
    width: 1200px; height: 900px; overflow: hidden;
    background: var(--backdrop);
    font-family: "Source Sans 3", "Myriad Pro", sans-serif;
  }
  .stage {
    position: relative; width: 1200px; height: 900px;
  }
  .card {
    position: absolute; top: 300px;
    width: 500px; height: 290px;
    background: var(--card);
    border-radius: 26px;
  }
  .card--back { left: 70px; }
  .card--front { left: 630px; }

  /* back side */
  .back-mark {
    position: absolute; left: 52px; top: 112px;
    display: flex; align-items: center; gap: 12px;
  }
  .mark-dot {
    width: 34px; height: 34px; border-radius: 50%;
    border: 5px solid var(--ring-grey);
  }
  .mark-name {
    color: var(--brand-blue); font-weight: 600; font-size: 26px;
  }
  .contact {
    position: absolute; left: 270px; top: 78px;
    color: var(--text-light); font-size: 15px; line-height: 1.45;
  }
  .contact__name {
    color: var(--brand-blue); font-weight: 600; font-size: 18px;
    margin-bottom: 6px;
  }
  .contact__phone {
    display: flex; align-items: center; gap: 6px; margin-bottom: 12px;
  }
  .contact__phone svg { width: 12px; height: 12px; fill: var(--brand-blue); }
  .contact__address { padding-left: 18px; }

  /* front side */
  .front-brand {
    position: absolute; inset: 0;
    display: flex; align-items: center; justify-content: center; gap: 14px;
  }
  .front-brand .mark-dot { width: 40px; height: 40px; border-width: 6px; }
  .front-brand .mark-name { font-size: 40px; }
</style>
</head>
<body>
<main class="stage">
  <section class="card card--back" aria-label="Card back">
    <div class="back-mark">
      <span class="mark-dot"></span>
      <span class="mark-name">Tidemark</span>
    </div>
    <div class="contact">
      <p class="contact__name">Rowan Tellick Builders</p>
      <p class="contact__phone">
        <svg viewBox="0 0 24 24" aria-hidden="true"><path d="M6.6 10.8a15.1 15.1 0 0 0 6.6 6.6l2.2-2.2a1 1 0 0 1 1-.25 11.4 11.4 0 0 0 3.6.57 1 1 0 0 1 1 1V20a1 1 0 0 1-1 1A17 17 0 0 1 3 4a1 1 0 0 1 1-1h3.5a1 1 0 0 1 1 1 11.4 11.4 0 0 0 .57 3.6 1 1 0 0 1-.25 1z"/></svg>
        021583917
      </p>
      <p class="contact__address">18 Kestrel Rd Harwood Bay<br>Auckland 0814<br>PO Box 927 Mangawhai 0583</p>
    </div>
  </section>

  <section class="card card--front" aria-label="Card front">
    <div class="front-brand">
      <span class="mark-dot"></span>
      <span class="mark-name">Tidemark Builders</span>
    </div>
  </section>
</main>
</body>
</html>
```